Threat Lens ratings for Apps and Games

I need a web site designing that is aimed at parents and will show an "Threat Lens" rating for apps and games. I have attached a document with an overview of what the Threat Lens is. The website needs to be easy for parents to navigate and find what they want quickly and easily. I should also be able to update the website myself easily with "reviews" of the attack vectors for apps and games.

Target Market(s)

Parents

Coding

Coded - Design and coding required

Number of Pages Required

2 page

Requirements
Must have
• Clear and concise ratings for apps and games

```html
<!DOCTYPE html>
<html lang="en">
<head>
<meta charset="utf-8">
<title>Threat Lens – App and Game Ratings for Parents</title>
<link href="https://fonts.googleapis.com/css2?family=Montserrat:wght@400;500;600;700&display=swap" rel="stylesheet">
<style>
  :root {
    --brand: #d94a0a;
    --brand-soft: #fbe8df;
    --ink: #111111;
    --text: #333333;
    --muted-bg: #f7f7f7;
    --white: #ffffff;
    --peach-glow: rgba(232, 120, 60, 0.35);
  }
  * { box-sizing: border-box; margin: 0; padding: 0; }
  html, body {
    width: 1200px; height: 3585px; overflow: hidden;
    font-family: 'Montserrat', sans-serif; color: var(--text); background: var(--white);
  }
  .page { position: relative; width: 1200px; height: 3585px; }
  .abs { position: absolute; }

  /* Header */
  .site-header { position: absolute; left: 0; top: 0; width: 1200px; height: 83px; background: var(--white); }
  .brand-name { position: absolute; left: 78px; top: 25px; font-size: 27px; font-weight: 500; color: var(--brand); letter-spacing: 0.5px; }
  .main-nav { position: absolute; left: 371px; top: 33px; display: flex; gap: 24px; font-size: 13px; color: #333; }
  .login-btn { position: absolute; left: 1019px; top: 24px; width: 105px; height: 32px; border-radius: 16px; background: var(--brand); color: var(--white); font-size: 14px; font-weight: 700; display: flex; align-items: center; padding-left: 22px; gap: 18px; }

  /* Hero */
  .hero { position: absolute; left: 0; top: 83px; width: 1200px; height: 524px; background: linear-gradient(100deg, #c9440a 0%, #e0651f 45%, #d85414 100%); }
  .hero-photo { position: absolute; left: 0; top: 0; width: 1200px; height: 524px; background: radial-gradient(ellipse at 70% 40%, rgba(240,140,70,0.55), rgba(200,70,10,0) 60%); }
  .hero-phone { position: absolute; left: 300px; top: 58px; width: 152px; height: 312px; border-radius: 26px; background: #1a1a1a; }
  .hero-phone-screen { position: absolute; left: 8px; top: 8px; right: 8px; bottom: 8px; border-radius: 20px; background: var(--white); display: flex; align-items: center; justify-content: center; text-align: center; font-size: 25px; line-height: 27px; font-weight: 500; color: var(--brand); }
  .hero-hand { position: absolute; left: 150px; top: 170px; width: 240px; height: 354px; border-radius: 120px 120px 0 0; background: linear-gradient(180deg, #f0a070, #e07a40); opacity: 0.85; }
  .hero-title { position: absolute; left: 552px; top: 276px; width: 400px; text-align: center; font-size: 44px; line-height: 50px; font-weight: 700; color: var(--white); }
  .hero-cta { position: absolute; left: 685px; top: 393px; width: 141px; height: 32px; border-radius: 16px; background: var(--ink); color: var(--white); font-size: 15px; font-weight: 700; text-align: center; line-height: 32px; }
  .hero-dots span { position: absolute; left: 1122px; width: 6px; height: 6px; border-radius: 50%; background: var(--ink); }

  /* Feature sections */
  .feature { position: absolute; left: 0; width: 1200px; }
  .feature.alt { background: var(--muted-bg); }
  .feature-icon { position: absolute; }
  .feature-title { position: absolute; font-size: 44px; line-height: 52px; font-weight: 700; color: var(--ink); }
  .feature-text { position: absolute; width: 445px; font-size: 15px; line-height: 27.8px; color: var(--text); }
  .read-more { position: absolute; width: 105px; height: 32px; border-radius: 16px; background: var(--ink); color: var(--white); font-size: 12px; font-weight: 700; text-align: center; line-height: 32px; }
  .photo { position: absolute; border-radius: 22px; box-shadow: 0 6px 28px var(--peach-glow); }
  .soft-shape { position: absolute; background: var(--brand-soft); }
  .ring { position: absolute; border-radius: 50%; border: 4px solid #e7793b; }

  /* Reviews */
  .reviews { position: absolute; left: 0; top: 2835px; width: 1200px; height: 527px; background: var(--brand); }
  .reviews-title { position: absolute; left: 0; top: 38px; width: 1200px; text-align: center; font-size: 50px; font-weight: 700; color: var(--white); }
  .review-card { position: absolute; top: 149px; width: 330px; height: 188px; background: var(--white); padding: 24px 28px; }
  .review-card::after { content: ""; position: absolute; left: 26px; bottom: -20px; border-left: 14px solid transparent; border-right: 14px solid transparent; border-top: 20px solid var(--white); }
  .stars { color: var(--brand); font-size: 15px; letter-spacing: 3px; }
  .review-text { margin-top: 12px; font-size: 12.5px; line-height: 22px; color: #333; }
  .reviewer { position: absolute; top: 362px; display: flex; align-items: center; gap: 18px; color: var(--white); }
  .avatar { width: 50px; height: 50px; border-radius: 50%; background: var(--white); display: flex; align-items: center; justify-content: center; }
  .reviewer-name { font-size: 15px; line-height: 20px; }
  .reviewer-role { font-size: 13px; line-height: 18px; }

  /* Footer */
  .site-footer { position: absolute; left: 0; top: 3362px; width: 1200px; height: 223px; background: var(--white); text-align: center; }
  .footer-brand { position: absolute; left: 0; top: 68px; width: 1200px; font-size: 27px; font-weight: 500; color: var(--brand); }
  .footer-social { position: absolute; left: 534px; top: 102px; display: flex; gap: 22px; }
  .footer-social span { width: 14px; height: 14px; border-radius: 50%; background: var(--brand); }
  .footer-nav { position: absolute; left: 0; top: 132px; width: 1200px; display: flex; justify-content: center; gap: 24px; font-size: 13px; color: #333; }
  .copyright { position: absolute; left: 0; top: 165px; width: 1200px; font-size: 13px; color: #333; }
</style>
</head>
<body>
<div class="page">

  <header class="site-header">
    <div class="brand-name">THREAT LENS</div>
    <nav class="main-nav">
      <span>Home</span><span>Chat/Messaging</span><span>Camera/Microphone Access</span><span>Location Services</span><span>Live Streaming</span>
    </nav>
    <div class="login-btn">Login
      <svg width="10" height="6" viewBox="0 0 10 6"><path d="M1 1l4 4 4-4" fill="none" stroke="#fff" stroke-width="1.5"/></svg>
    </div>
  </header>

  <section class="hero">
    <div class="hero-photo" role="img" aria-label="Parent and child looking at a phone together, orange tinted"></div>
    <div class="hero-hand" role="img" aria-label="Hand holding a phone"></div>
    <div class="hero-phone"><div class="hero-phone-screen">THREAT<br>LENS</div></div>
    <h1 class="hero-title">Lorium ipsum dolor amit</h1>
    <div class="hero-cta">Get Started</div>
    <div class="hero-dots">
      <span style="top:219px"></span><span style="top:239px"></span>
      <span style="top:258px;background:#3a8f96"></span>
      <span style="top:277px"></span><span style="top:297px"></span>
    </div>
  </section>

  <!-- Chat / Messaging -->
  <section class="feature" style="top:607px;height:523px;">
    <svg class="feature-icon" style="left:83px;top:143px" width="22" height="20" viewBox="0 0 22 20"><path d="M11 1C5.5 1 1 4.6 1 9c0 2.2 1.1 4.2 3 5.6L3 19l5-2.6c1 .3 2 .4 3 .4 5.5 0 10-3.6 10-8S16.5 1 11 1z" fill="var(--brand)"/></svg>
    <h2 class="feature-title" style="left:76px;top:170px">Chat / Messaging</h2>
    <p class="feature-text" style="left:79px;top:239px">Lorem ipsum dolor sit amet, consectetur adipiscing elit, sed do eiusmod tempor incididunt ut labore et dolore magna aliqua. Ut enim ad minim veniam, quis nostrud exercitation ullamco laboris</p>
    <div class="read-more" style="left:76px;top:373px">Read more</div>
    <svg class="abs" style="left:525px;top:90px" width="520" height="320" viewBox="0 0 520 320"><path d="M150 20h250a100 100 0 0 1 100 100v40a100 100 0 0 1-100 100H170l-160 40 70-70A100 100 0 0 1 50 160v-40A100 100 0 0 1 150 20z" fill="none" stroke="var(--brand-soft)" stroke-width="34"/></svg>
    <div class="ring" style="left:583px;top:221px;width:20px;height:20px"></div>
    <div class="photo" style="left:620px;top:101px;width:323px;height:232px;background:linear-gradient(135deg,#1a1f6e,#3440c8 55%,#0c0c2a)" role="img" aria-label="Child using a phone under a blanket at night"></div>
    <div class="photo" style="left:848px;top:224px;width:183px;height:231px;background:linear-gradient(160deg,#e8d8c8,#c89068 55%,#e8b030)" role="img" aria-label="Parent and daughter looking at a phone"></div>
    <div class="ring" style="left:990px;top:201px;width:38px;height:38px;border-width:5px"></div>
  </section>

  <!-- Camera / Microphone -->
  <section class="feature alt" style="top:1130px;height:578px;">
    <div class="soft-shape" style="left:126px;top:83px;width:344px;height:380px;border-radius:34px"></div>
    <div class="photo" style="left:123px;top:134px;width:322px;height:232px;background:linear-gradient(135deg,#fbe04a,#f5c21e 60%,#e85a9a)" role="img" aria-label="Girl taking a selfie against a yellow background"></div>
    <div class="photo" style="left:378px;top:280px;width:184px;height:230px;background:linear-gradient(160deg,#e42a2a,#c41818 60%,#7a1a1a)" role="img" aria-label="Laughing girl holding a phone against a red background"></div>
    <svg class="abs" style="left:500px;top:138px" width="92" height="126" viewBox="0 0 92 126"><rect x="28" y="2" width="36" height="70" rx="18" fill="var(--brand)"/><path d="M10 52a36 36 0 0 0 72 0" fill="none" stroke="var(--brand)" stroke-width="10"/><rect x="41" y="88" width="10" height="20" fill="var(--brand)"/><rect x="22" y="108" width="48" height="10" rx="5" fill="var(--brand)"/></svg>
    <svg class="feature-icon" style="left:690px;top:102px" width="22" height="19" viewBox="0 0 22 19"><path d="M7 2h8l2 3h3a2 2 0 0 1 2 2v10a2 2 0 0 1-2 2H2a2 2 0 0 1-2-2V7a2 2 0 0 1 2-2h3z" fill="var(--brand)"/><circle cx="11" cy="11" r="4" fill="var(--muted-bg)"/><circle cx="11" cy="11" r="2.2" fill="var(--brand)"/></svg>
    <h2 class="feature-title" style="left:684px;top:134px">Camera<br>Microphone Access</h2>
    <p class="feature-text" style="left:687px;top:246px">Lorem ipsum dolor sit amet, consectetur adipiscing elit, sed do eiusmod tempor incididunt ut labore et dolore magna aliqua. Ut enim ad minim veniam, quis nostrud exercitation ullamco laboris</p>
    <div class="read-more" style="left:684px;top:379px">Read more</div>
  </section>

  <!-- Location -->
  <section class="feature" style="top:1708px;height:550px;">
    <svg class="feature-icon" style="left:78px;top:46px" width="26" height="20" viewBox="0 0 26 20"><path d="M1 3l7-2v16l-7 2zM9 1l8 2v16l-8-2zM18 3l7-2v16l-7 2z" fill="var(--brand)"/></svg>
    <h2 class="feature-title" style="left:73px;top:76px">Location Services</h2>
    <p class="feature-text" style="left:76px;top:145px">Lorem ipsum dolor sit amet, consectetur adipiscing elit, sed do eiusmod tempor incididunt ut labore et dolore magna aliqua. Ut enim ad minim veniam, quis nostrud exercitation ullamco laboris</p>
    <div class="read-more" style="left:73px;top:277px">Read more</div>
    <div class="abs" style="left:447px;top:320px;width:753px;height:180px;background:linear-gradient(180deg,rgba(230,230,230,0),rgba(225,225,225,0.6))" role="img" aria-label="Faint topographic contour lines"></div>
    <svg class="abs" style="left:580px;top:37px" width="290" height="430" viewBox="0 0 290 430"><path d="M145 0A145 145 0 0 0 0 145c0 110 145 285 145 285s145-175 145-285A145 145 0 0 0 145 0zm0 80a65 65 0 1 1 0 130 65 65 0 0 1 0-130z" fill="var(--brand-soft)" opacity="0.8"/></svg>
    <div class="abs" style="left:745px;top:75px;width:172px;height:357px;border-radius:26px;background:#1a1a1a;padding:8px">
      <div style="width:100%;height:100%;border-radius:20px;background:linear-gradient(180deg,#eef0f3,#d9dde3)" role="img" aria-label="Map app showing a route with a red location pin"></div>
    </div>
  </section>

  <!-- Live Streaming -->
  <section class="feature alt" style="top:2258px;height:577px;">
    <div class="soft-shape" style="left:111px;top:117px;width:491px;height:327px;border-radius:34px"></div>
    <div class="photo" style="left:164px;top:66px;width:322px;height:232px;background:linear-gradient(135deg,#d8dce4,#b8c0cc 50%,#e8a8b8)" role="img" aria-label="Young woman streaming with a phone on a tripod"></div>
    <div class="photo" style="left:377px;top:242px;width:184px;height:230px;background:linear-gradient(160deg,#d8dde4,#9aa7b6 55%,#2a5a9a)" role="img" aria-label="Boy with headphones holding a phone"></div>
    <svg class="feature-icon" style="left:690px;top:82px" width="26" height="17" viewBox="0 0 26 17"><rect x="0" y="0" width="18" height="17" rx="3" fill="var(--brand)"/><path d="M19 6l7-4v13l-7-4z" fill="var(--brand)"/></svg>
    <h2 class="feature-title" style="left:684px;top:104px">Live Streming</h2>
    <p class="feature-text" style="left:687px;top:172px">Lorem ipsum dolor sit amet, consectetur adipiscing elit, sed do eiusmod tempor incididunt ut labore et dolore magna aliqua. Ut enim ad minim veniam, quis nostrud exercitation ullamco laboris</p>
    <div class="read-more" style="left:684px;top:304px">Read more</div>
  </section>

  <!-- Reviews -->
  <section class="reviews">
    <h2 class="reviews-title">Reviews</h2>
    <article class="review-card" style="left:74px">
      <div class="stars">★★★★★</div>
      <p class="review-text">omnis iste natus error sit voluptatem accu-santium doloremque laudantium totam rem aperiam eaque ipsa quae ab illo inventore veritatis et quasi.</p>
    </article>
    <article class="review-card" style="left:435px">
      <div class="stars">★★★★★</div>
      <p class="review-text">omnis iste natus error sit voluptatem accu-santium doloremque laudantium totam rem aperiam eaque ipsa quae ab illo inventore veritatis et quasi.</p>
    </article>
    <article class="review-card" style="left:796px">
      <div class="stars">★★★★★</div>
      <p class="review-text">omnis iste natus error sit voluptatem accu-santium doloremque laudantium totam rem aperiam eaque ipsa quae ab illo inventore veritatis et quasi.</p>
    </article>
    <div class="reviewer" style="left:92px">
      <div class="avatar"><svg width="20" height="20" viewBox="0 0 20 20"><circle cx="10" cy="6" r="4.5" fill="none" stroke="#666" stroke-width="1.4"/><path d="M2 19c0-4.4 3.6-7 8-7s8 2.6 8 7z" fill="none" stroke="#666" stroke-width="1.4"/></svg></div>
      <div><div class="reviewer-name">Daniel Harper</div><div class="reviewer-role">Customer</div></div>
    </div>
    <div class="reviewer" style="left:453px">
      <div class="avatar"><svg width="20" height="20" viewBox="0 0 20 20"><circle cx="10" cy="6" r="4.5" fill="none" stroke="#666" stroke-width="1.4"/><path d="M2 19c0-4.4 3.6-7 8-7s8 2.6 8 7z" fill="none" stroke="#666" stroke-width="1.4"/></svg></div>
      <div><div class="reviewer-name">Nina Ford</div><div class="reviewer-role">Customer</div></div>
    </div>
    <div class="reviewer" style="left:814px">
      <div class="avatar"><svg width="20" height="20" viewBox="0 0 20 20"><circle cx="10" cy="6" r="4.5" fill="none" stroke="#666" stroke-width="1.4"/><path d="M2 19c0-4.4 3.6-7 8-7s8 2.6 8 7z" fill="none" stroke="#666" stroke-width="1.4"/></svg></div>
      <div><div class="reviewer-name">Owen Blake</div><div class="reviewer-role">Customer</div></div>
    </div>
  </section>

  <footer class="site-footer">
    <div class="footer-brand">THREAT LENS</div>
    <div class="footer-social"><span></span><span></span><span></span><span></span></div>
    <nav class="footer-nav"><span>Home</span><span>Chat/Messaging</span><span>Camera/Microphone Access</span><span>Location Services</span><span>Live Streaming</span></nav>
    <div class="copyright">© 2021 &nbsp;|&nbsp; www.threatlens-example.com</div>
  </footer>

</div>
</body>
</html>
```